Campaign Website

I need a website for my judicial campaign. I would like a site that directs from this domain as well as a new domain with my married last name. I need separate pages on the site that address my diversion programs, and a page to allow people to donate with a link to my bank account and a link for people to submit requests to volunteer, get yard signs, etc.

```html
<!DOCTYPE html>
<html lang="en">
<head>
<meta charset="utf-8">
<title>Judge Danielle Harper Campaign</title>
<link rel="stylesheet" href="https://fonts.googleapis.com/css2?family=Archivo:wght@400;700;800&family=Lato:wght@400;700&family=Arimo:wght@400;700&family=Raleway:wght@600&display=swap">
<style>
:root{
  --red:#d4544b;
  --red-soft:#dc6a61;
  --ink:#111111;
  --text:#333333;
  --muted:#666666;
  --grey-bg:#efefef;
  --dark:#1a1a1a;
  --charcoal:#4a4a4d;
  --white:#ffffff;
  --wood-1:#3a2a22;
  --wood-2:#6b5040;
}
*{margin:0;padding:0;box-sizing:border-box}
html,body{width:1200px;height:2915px;overflow:hidden}
body{position:relative;background:var(--white);font-family:'Lato',sans-serif;color:var(--text)}
.abs{position:absolute}

/* hero */
.hero{left:0;top:0;width:1200px;height:780px;background:linear-gradient(100deg,var(--wood-1) 0%,var(--wood-2) 45%,#8a6a55 70%,var(--wood-1) 100%)}
.hero-couple{left:540px;top:110px;width:560px;height:670px;border-radius:260px 260px 0 0;background:linear-gradient(180deg,#c9a88f 0%,#e9e1d2 45%,#7a6a44 100%);opacity:.85}
.brand{left:141px;top:34px;font-family:'Raleway',sans-serif;font-weight:600;font-size:29px;color:var(--white)}
.nav{left:436px;top:42px;display:flex;gap:30px;font-family:'Arimo',sans-serif;font-weight:700;font-size:15.5px;color:var(--white)}
.nav a{color:inherit;text-decoration:none;position:relative;padding-bottom:14px}
.nav a.active{color:var(--red-soft)}
.nav a.active::after{content:"";position:absolute;left:-4px;right:-4px;bottom:0;height:3px;background:var(--white)}
.hero-copy{left:130px;top:262px;width:430px;text-align:center;color:var(--white);font-family:'Archivo',sans-serif}
.hero-copy .welcome{font-weight:400;font-size:31px;letter-spacing:.5px}
.hero-copy h1{font-weight:800;font-size:38px;line-height:42px;margin-top:6px}
.btn{display:inline-block;border-radius:30px;font-family:'Lato',sans-serif;font-weight:700;text-align:center;text-decoration:none}
.btn-donate{margin-top:19px;width:180px;height:60px;line-height:60px;background:var(--red);color:var(--white);font-size:21px}
.arrow{width:57px;height:57px;border-radius:50%;background:rgba(220,220,220,.55);top:331px}
.arrow svg{position:absolute;left:18px;top:17px}

/* about */
.about-photo{left:158px;top:777px;width:374px;height:374px;border-radius:50%;border:2px solid #dcdcdc;background:var(--white);box-shadow:0 4px 14px rgba(0,0,0,.08)}
.about-photo .fill{position:absolute;left:12px;top:12px;width:346px;height:346px;border-radius:50%;background:radial-gradient(circle at 50% 40%,#6b4a3a 0%,#2b2b2b 60%,#111 100%)}
.about{left:553px;top:808px;width:480px}
h2{font-family:'Archivo',sans-serif;font-weight:800;color:var(--ink)}
.about h2{font-size:38px}
.about p{font-size:16.5px;line-height:22px;margin-top:12px;color:var(--text)}
.about p:first-of-type{margin-top:22px}
.btn-red{background:var(--red);color:var(--white)}
.about .btn{margin-top:30px;width:162px;height:54px;line-height:54px;font-size:16px}

/* judicial */
.campaign{left:0;top:1200px;width:1200px;height:570px}
.campaign-copy{left:200px;top:1325px;width:800px;text-align:center;color:var(--white)}
.campaign-copy h2{color:var(--white);font-size:37px}
.campaign-copy p{font-size:19.5px;line-height:29px;margin-top:14px}
.campaign-copy p:first-of-type{margin-top:22px}
.btn-white{background:var(--white);color:var(--red);margin-top:30px;width:168px;height:55px;line-height:55px;font-size:16px}

/* diversion */
.diversion{left:175px;top:1866px;width:400px}
.diversion h2{font-size:29px}
.diversion p{font-size:15px;line-height:22px;margin-top:12px;color:var(--text)}
.diversion p:first-of-type{margin-top:20px}
.diversion .btn{margin-top:24px;margin-left:-4px;width:147px;height:49px;line-height:49px;font-size:15px}
.diversion-frame{left:601px;top:1856px;width:411px;height:278px;border-left:5px solid var(--red);border-bottom:5px solid var(--red)}
.diversion-photo{left:617px;top:1843px;width:411px;height:274px;background:linear-gradient(135deg,#8f8f5e 0%,#5a4d44 50%,#3c3a4a 100%)}

/* blogs */
.blogs-bg{left:0;top:2190px;width:1200px;height:600px}
.blogs-title{left:0;top:2270px;width:1184px;text-align:center;font-size:30px}
.card{top:2349px;width:272px}
.card .photo{position:relative;height:170px;background:linear-gradient(135deg,#6b5a52,#a08878)}
.card .date{position:absolute;left:16px;top:14px;width:44px;height:50px;border-radius:6px;background:var(--red-soft);color:var(--white);text-align:center;font-family:'Lato',sans-serif}
.card .date small{display:block;font-size:10px;padding-top:6px}
.card .date b{display:block;font-size:18px;line-height:20px;font-weight:400}
.card h3{margin-top:20px;font-family:'Lato',sans-serif;font-weight:400;font-size:18.5px;line-height:24px;color:var(--text)}
.card .meta{margin-top:14px;font-size:11px;color:var(--text);display:flex;align-items:center;gap:6px}
.card .excerpt{margin-top:14px;font-size:13.5px;line-height:21px;color:var(--muted)}

/* footer */
.footer-bg{left:0;top:2660px;width:1200px;height:255px}
.footer-nav{left:173px;top:2815px;display:flex;gap:30px;font-family:'Arimo',sans-serif;font-weight:700;font-size:16px;color:var(--white)}
.footer-nav a{color:inherit;text-decoration:none}
.copyright{left:168px;top:2845px;font-family:'Arimo',sans-serif;font-size:13px;color:var(--white)}
.social{left:892px;top:2814px;display:flex;gap:36px}
.social span{display:block;width:20px;height:20px;border-radius:50%;background:var(--white)}
</style>
</head>
<body>

<!-- hero -->
<div class="abs hero" role="img" aria-label="Photo of the candidate embracing her husband in front of a wooden fence"></div>
<div class="abs hero-couple" role="img" aria-label="Smiling couple hugging"></div>
<div class="abs brand">Harper Danielle</div>
<nav class="abs nav">
  <a class="active" href="#">Biography</a><a href="#">Events</a><a href="#">Endorsements</a><a href="#">Voting Information</a><a href="#">Donate</a><a href="#">Contact</a>
</nav>
<div class="abs arrow" style="left:62px"><svg width="20" height="22" viewBox="0 0 20 22"><path d="M13 2 L4 11 L13 20" fill="none" stroke="#222" stroke-width="3"/></svg></div>
<div class="abs arrow" style="left:1077px"><svg width="20" height="22" viewBox="0 0 20 22"><path d="M6 2 L15 11 L6 20" fill="none" stroke="#222" stroke-width="3"/></svg></div>
<div class="abs hero-copy">
  <div class="welcome">WELCOME TO</div>
  <h1>JUDGE DANIELLE<br>HARPER CAMPAIGN</h1>
  <a class="btn btn-donate" href="#">DONATE</a>
</div>
<svg class="abs" style="left:0;top:680px" width="1200" height="120" viewBox="0 0 1200 120">
  <path d="M0,90 Q600,-30 1200,82 L1200,120 L0,120 Z" fill="var(--red)"/>
  <path d="M0,102 Q600,-8 1200,96 L1200,120 L0,120 Z" fill="var(--white)"/>
</svg>

<!-- about -->
<div class="abs about-photo"><div class="fill" role="img" aria-label="Portrait of the judge in her robe"></div></div>
<section class="abs about">
  <h2>ABOUT ME</h2>
  <p>My candidacy is based on the belief that the judiciary needs to be accountable to the citizens it serves.</p>
  <p>This starts with being present and accessible to ensure that both victims of crime, as well as those accused, have their day in court without unnecessary delays.&nbsp; Additionally, it is incumbent upon the judiciary to be proactive and innovative by starting</p>
  <a class="btn btn-red" href="#">READ MORE</a>
</section>

<!-- judicial campaign -->
<svg class="abs campaign" viewBox="0 0 1200 570" role="img" aria-label="Group photo of campaign supporters under a red overlay">
  <defs>
    <linearGradient id="fadeTop" x1="0" y1="0" x2="0" y2="1">
      <stop offset="0" stop-color="#ffffff" stop-opacity="0"/>
      <stop offset="1" stop-color="#f6f6f6"/>
    </linearGradient>
  </defs>
  <rect x="0" y="-60" width="1200" height="80" fill="url(#fadeTop)"/>
  <path d="M0,170 Q250,30 620,8 Q900,-6 1200,20 L1200,470 Q700,600 0,558 Z" fill="var(--charcoal)"/>
  <path d="M0,200 Q300,30 700,8 Q950,0 1200,20 L1200,430 Q700,560 0,548 Z" fill="var(--red)"/>
  <path d="M0,200 Q300,30 700,8 Q950,0 1200,20 L1200,430 Q700,560 0,548 Z" fill="#ffffff" opacity=".06"/>
</svg>
<section class="abs campaign-copy">
  <h2>JUDICIAL CAMPAIGN</h2>
  <p>Pellentesque faucibus Ut accumsan ultricies elit Maecenas at justo id velit placerat molestie Donec dictum lectus non odio</p>
  <p>Cras a ante vitae enim iaculis aliquam Mauris nunc &nbsp;est nunc venenatis in tristique eu imperdiet ac nisl Cum sociis natoque penatibus et magnis dis parturient montes nascetur ridiculus mus In iaculis facilisis massa Etiam eu</p>
  <a class="btn btn-white" href="#">READ MORE</a>
</section>

<!-- diversion programs -->
<section class="abs diversion">
  <h2>MY DIVERSION PROGRAMS</h2>
  <p>Curabitur iaculis tempus eros Curabitur vel mi sit amet magna malesuada ultrices Ut nisi erat fermentum vel</p>
  <p>Aongue id euismod in elit Fusce ultricies orci ac feugiat suscipit leo massa sodales velit et scelerisque mi tortor at ipsum Proin orci odio commodo ac gravida no</p>
  <a class="btn btn-red" href="#">READ MORE</a>
</section>
<div class="abs diversion-frame"></div>
<div class="abs diversion-photo" role="img" aria-label="Students seated in a circle during a diversion program session"></div>

<!-- recent blogs -->
<svg class="abs blogs-bg" viewBox="0 0 1200 600">
  <path d="M0,150 Q500,-10 1200,13 L1200,600 L0,600 Z" fill="var(--red)"/>
  <path d="M0,170 Q500,4 1200,18 L1200,600 L0,600 Z" fill="var(--grey-bg)"/>
</svg>
<h2 class="abs blogs-title">RECENT BLOGS</h2>

<article class="abs card" style="left:160px">
  <div class="photo" role="img" aria-label="Guests at a banquet event"><div class="date"><small>Mar</small><b>30</b></div></div>
  <h3>Minus id quod maxime placeat Facere possimus</h3>
  <div class="meta"><svg width="9" height="10" viewBox="0 0 9 10"><circle cx="4.5" cy="3" r="2.5" fill="#555"/><path d="M0,10 Q4.5,3 9,10Z" fill="#555"/></svg>Arjun&nbsp; | &nbsp;<svg width="12" height="10" viewBox="0 0 12 10"><ellipse cx="6" cy="4.5" rx="5" ry="3.5" fill="none" stroke="#555" stroke-width="1.4"/></svg>214 Comments</div>
  <p class="excerpt">Nam libero tempore, cum soluta nobis est eli gendi optio cumque nihil impedit.</p>
</article>
<article class="abs card" style="left:464px">
  <div class="photo" role="img" aria-label="The candidate with a supporter" style="background:linear-gradient(135deg,#4a3a35,#d8d2cc 60%,#6a5048)"><div class="date"><small>Mar</small><b>30</b></div></div>
  <h3>Minus id quod maxime placeat Facere possimus</h3>
  <div class="meta"><svg width="9" height="10" viewBox="0 0 9 10"><circle cx="4.5" cy="3" r="2.5" fill="#555"/><path d="M0,10 Q4.5,3 9,10Z" fill="#555"/></svg>Arjun&nbsp; | &nbsp;<svg width="12" height="10" viewBox="0 0 12 10"><ellipse cx="6" cy="4.5" rx="5" ry="3.5" fill="none" stroke="#555" stroke-width="1.4"/></svg>214 Comments</div>
  <p class="excerpt">Nam libero tempore, cum soluta nobis est eli gendi optio cumque nihil impedit.</p>
</article>
<article class="abs card" style="left:768px">
  <div class="photo" role="img" aria-label="Schoolchildren in a classroom" style="background:linear-gradient(135deg,#6a8a5a,#a84040 55%,#3a3a4a)"><div class="date"><small>Mar</small><b>30</b></div></div>
  <h3>Minus id quod maxime placeat Facere possimus</h3>
  <div class="meta"><svg width="9" height="10" viewBox="0 0 9 10"><circle cx="4.5" cy="3" r="2.5" fill="#555"/><path d="M0,10 Q4.5,3 9,10Z" fill="#555"/></svg>Arjun&nbsp; | &nbsp;<svg width="12" height="10" viewBox="0 0 12 10"><ellipse cx="6" cy="4.5" rx="5" ry="3.5" fill="none" stroke="#555" stroke-width="1.4"/></svg>214 Comments</div>
  <p class="excerpt">Nam libero tempore, cum soluta nobis est eli gendi optio cumque nihil impedit.</p>
</article>

<!-- footer -->
<svg class="abs footer-bg" viewBox="0 0 1200 255">
  <path d="M0,100 Q800,110 1200,0 L1200,255 L0,255 Z" fill="var(--red)"/>
  <path d="M0,100 Q850,108 1200,32 L1200,255 L0,255 Z" fill="var(--dark)"/>
</svg>
<nav class="abs footer-nav">
  <a href="#">Biography</a><a href="#">Events</a><a href="#">Endorsements</a><a href="#">Voting Information</a><a href="#">Donate</a><a href="#">Contact</a>
</nav>
<div class="abs copyright">© 2019 Company Name&nbsp; All right reserved</div>
<div class="abs social" aria-label="Social links"><span></span><span></span><span></span></div>

</body>
</html>
```